"Vine Hollow Excursions" is a top notch Santa Barbara County Wine Tour company.

We provide scenic, boutique and custom wine tours. I need the card to be clean and classy. I will provide our logo. I would like the logo to cover the back side of the card as an option and would like to see a couple color options other then our signature green and gold. I would like to see some creative options and let the designers come up with options.
I need cards for myself and my team. The final design should communicate "An authentic and boutique wine tour experience"
Please use my website for reference www.vinehollowexcursions.example

Target Market(s)

We have a wide range of clients from millennials to baby boomers

Industry/Entity Type

Tour

Contact Information for Business Card

Contact info:
Dale Morton
805-219-6384
info@vinehollowexcursions.example
vinehollowexcursions.example

Colors

Designer to choose colors to be used in the design.

Requirements
Must have
• my logo
Nice to have
• *I would like to have the backside side with the logo and the company statement
• "An authentic and boutique wine tour experience" as an option.
• *I would also like to see what the designers can create!
• *I would like to see an option that incorporates or social: instagram, yelp, trip advisor
Should not have
• I do not want it too busy.

```html
<!DOCTYPE html>
<html lang="en">
<head>
<meta charset="utf-8">
<title>Vine Hollow Excursions – Business Card</title>
<link href="https://fonts.googleapis.com/css2?family=Cinzel:wght@400&family=Roboto+Condensed:wght@400&family=Roboto:wght@400&display=swap" rel="stylesheet">
<style>
  :root {
    --backdrop: #ebe8e4;
    --card-light: #ffffff;
    --card-shade: #dedede;
    --vine-green: #236a44;
    --gold: #a48b68;
    --gold-dark: #8a7559;
    --ink: #555555;
    --icon: #8c7f6d;
    --social: #7a7a7a;
  }
  * { margin: 0; padding: 0; box-sizing: border-box; }
  html, body { width: 1200px; height: 960px; overflow: hidden; }
  body { background: var(--backdrop); position: relative; }

  .card {
    position: absolute;
    width: 600px;
    height: 343px;
    background: linear-gradient(90deg, var(--card-light) 0%, #f2f2f2 50%, var(--card-shade) 100%);
    box-shadow: 2px 3px 6px rgba(0,0,0,0.25);
  }
  .card--front { left: 302px; top: 129px; }
  .card--back  { left: 299px; top: 488px; }

  .brand-name {
    position: absolute;
    font-family: "Cinzel", serif;
    font-weight: 400;
    white-space: nowrap;
  }
  .card--front .brand-name {
    left: 58px; top: 120px;
    font-size: 21px;
    letter-spacing: 1px;
    color: var(--gold);
  }

  .holder-name {
    position: absolute;
    left: 58px; top: 240px;
    font-family: "Roboto Condensed", sans-serif;
    font-size: 27px;
    color: var(--gold-dark);
    letter-spacing: -0.3px;
  }
  .holder-rule {
    position: absolute;
    left: 0; top: 276px;
    width: 205px; height: 1px;
    background: #444;
  }

  .contact-list {
    position: absolute;
    left: 336px; top: 242px;
    list-style: none;
    font-family: "Roboto", sans-serif;
    font-size: 13.5px;
    color: var(--ink);
  }
  .contact-list li {
    display: flex; align-items: center;
    height: 19px;
    white-space: nowrap;
  }
  .contact-list svg { width: 13px; height: 13px; margin-right: 8px; fill: var(--icon); }

  .card--back .brand-name {
    left: 0; right: 0; top: 120px;
    text-align: center;
    font-size: 33px;
    letter-spacing: 1px;
    color: var(--vine-green);
  }
  .tagline {
    position: absolute;
    left: 0; right: 0; top: 218px;
    text-align: center;
    font-family: "Roboto Condensed", sans-serif;
    font-size: 16px;
    color: var(--gold-dark);
  }
  .social-row {
    position: absolute;
    left: 221px; top: 282px;
    display: flex; gap: 7px;
  }
  .social-badge {
    width: 27px; height: 27px;
    border-radius: 4px;
    background: linear-gradient(180deg, #9a9a9a, var(--social));
  }
</style>
</head>
<body>
  <section class="card card--front" aria-label="Card front">
    <div class="brand-name">Vine Hollow Excursions</div>
    <div class="holder-name">DALE MORTON</div>
    <div class="holder-rule"></div>
    <ul class="contact-list">
      <li>
        <svg viewBox="0 0 16 16" aria-hidden="true"><path d="M3.6 1.2l2.3 2.6c.4.4.4 1 0 1.4L4.6 6.5c.9 2 2.6 3.7 4.7 4.7l1.3-1.3c.4-.4 1-.4 1.4 0l2.6 2.3c.4.4.4 1 0 1.4l-1.2 1.2c-.6.6-1.5.8-2.3.5C6.3 13.6 2.4 9.7.7 4.9.4 4.1.6 3.2 1.2 2.6L2.2 1.2c.4-.4 1-.4 1.4 0z"/></svg>
        805-219-6384
      </li>
      <li>
        <svg viewBox="0 0 16 16" aria-hidden="true"><path d="M1 3h14v10H1z M2 4.2v.3l6 4 6-4v-.3z" fill-rule="evenodd"/></svg>
        info@vinehollowexcursions.example
      </li>
      <li>
        <svg viewBox="0 0 16 16" aria-hidden="true"><circle cx="8" cy="8" r="7"/></svg>
        vinehollowexcursions.example
      </li>
    </ul>
  </section>

  <section class="card card--back" aria-label="Card back">
    <div class="brand-name">Vine Hollow Excursions</div>
    <p class="tagline">An authentic &amp; boutique wine tour experience</p>
    <div class="social-row" aria-label="Social profiles">
      <span class="social-badge"></span>
      <span class="social-badge"></span>
      <span class="social-badge"></span>
      <span class="social-badge"></span>
      <span class="social-badge"></span>
    </div>
  </section>
</body>
</html>
```